Diagram of Hollowmere’s history for website

This project is to design the attached diagram along the lines of the attached image but in our branding - style guide attached. The diagram will be going on the Hollowmere website - www.hollowmere.au.

```html
<!DOCTYPE html>
<html lang="en">
<head>
<meta charset="utf-8">
<title>Hollowmere's History</title>
<link rel="stylesheet" href="https://fonts.googleapis.com/css2?family=Poppins:wght@400;600;700&display=swap">
<style>
  :root {
    --green-deep: #566f5a;
    --green-sage: #74917a;
    --blue-mist: #7f9ea6;
    --slate: #667d80;
    --clay: #ab8a7d;
    --sand: #d9b29e;
    --ink: #444444;
    --paper: #ffffff;
  }
  html, body { margin: 0; padding: 0; overflow: hidden; }
  body { width: 1200px; height: 1200px; background: var(--paper); }
  .history-canvas { position: relative; width: 1200px; height: 1200px; background: var(--paper); }
  .history-diagram { position: absolute; left: 0; top: 136px; width: 1200px; height: 928px; }
  text { font-family: 'Poppins', sans-serif; }
  .title { font-size: 80px; font-weight: 700; letter-spacing: 1px; }
  .title-brand { fill: var(--green-deep); }
  .title-word { fill: var(--clay); }
  .year { font-size: 19px; font-weight: 600; fill: var(--paper); }
  .event-title { font-size: 20px; font-weight: 600; }
  .event-body { font-size: 13.5px; fill: var(--ink); }
  .connector { fill: none; stroke-width: 1.3; }
  .node { fill: var(--paper); stroke-width: 1.3; }
  .c-2017 { fill: var(--sand); } .s-2017 { stroke: var(--sand); }
  .c-2018 { fill: var(--green-sage); } .s-2018 { stroke: var(--green-sage); }
  .c-2019 { fill: var(--blue-mist); } .s-2019 { stroke: var(--blue-mist); }
  .c-2021 { fill: var(--clay); } .s-2021 { stroke: var(--clay); }
  .c-2022 { fill: var(--green-deep); } .s-2022 { stroke: var(--green-deep); }
  .c-2023 { fill: var(--slate); } .s-2023 { stroke: var(--slate); }
</style>
</head>
<body>
<div class="history-canvas">
<svg class="history-diagram" viewBox="100 248 1300 1005" xmlns="http://www.w3.org/2000/svg">
  <text class="title" x="750" y="406" text-anchor="middle"><tspan class="title-brand">HOLLOWMERE’S</tspan> <tspan class="title-word">HISTORY</tspan></text>

  <!-- timeline spine -->
  <polygon class="c-2017" points="681,490 693,504 706,490 706,576 693,590 681,576"/>
  <polygon class="c-2018" points="681,596 693,610 706,596 706,682 693,696 681,682"/>
  <polygon class="c-2019" points="681,700 693,714 706,700 706,786 693,800 681,786"/>
  <polygon class="c-2021" points="681,805 693,819 706,805 706,889 693,903 681,889"/>
  <polygon class="c-2022" points="681,907 693,921 706,907 706,991 693,1005 681,991"/>
  <polygon class="c-2023" points="681,1008 693,1022 706,1008 706,1093 693,1107 681,1093"/>

  <!-- 2017 -->
  <polyline class="connector s-2017" points="753,527 753,604 1186,604"/>
  <rect class="c-2017" x="718" y="500" width="90" height="27" rx="13.5"/>
  <circle class="node s-2017" cx="716" cy="513" r="4"/>
  <text class="year" x="763" y="521" text-anchor="middle">2017</text>
  <text class="event-title c-2017" x="816" y="516">Hollowmere Commences</text>
  <text class="event-body" x="816" y="536">Maren started the business with 25 years’ experience</text>
  <text class="event-body" x="816" y="552">working for government &amp;  non-government disability &amp;</text>
  <text class="event-body" x="816" y="568">community services. Our first office is in Ashvale</text>
  <text class="event-body" x="816" y="584">NCAS Provider</text>

  <!-- 2018 -->
  <polyline class="connector s-2018" points="628,628 628,701 197,701"/>
  <rect class="c-2018" x="580" y="601" width="88" height="27" rx="13.5"/>
  <circle class="node s-2018" cx="670" cy="614" r="4"/>
  <text class="year" x="624" y="622" text-anchor="middle">2018</text>
  <text class="event-title c-2018" x="558" y="612" text-anchor="end">Clinic Expansion</text>
  <text class="event-body" x="557" y="630" text-anchor="end">Hollowmere moves offices twice in Ashvale due to  growth &amp;</text>
  <text class="event-body" x="557" y="646" text-anchor="end">expansion.  Clinic established</text>

  <!-- 2019 -->
  <polyline class="connector s-2019" points="753,740 753,815 1186,815"/>
  <rect class="c-2019" x="718" y="713" width="90" height="27" rx="13.5"/>
  <circle class="node s-2019" cx="716" cy="726" r="4"/>
  <text class="year" x="763" y="734" text-anchor="middle">2019</text>
  <text class="event-title c-2019" x="816" y="727">Move to Brindlewood</text>
  <text class="event-body" x="816" y="746">Hollowmere moves to  Brindlewood due to further</text>
  <text class="event-body" x="816" y="762">growth &amp; expansion</text>

  <!-- 2021 -->
  <polyline class="connector s-2021" points="628,839 628,913 197,913"/>
  <rect class="c-2021" x="580" y="812" width="88" height="27" rx="13.5"/>
  <circle class="node s-2021" cx="670" cy="825" r="4"/>
  <text class="year" x="624" y="833" text-anchor="middle">2021</text>
  <text class="event-title c-2021" x="561" y="831" text-anchor="end">Purpose-Corporation</text>
  <text class="event-body" x="561" y="850" text-anchor="end">Hollowmere becomes an accredited Purpose-Corporation</text>
  <text class="event-body" x="561" y="867" text-anchor="end">having met the highest standards of environmental</text>
  <text class="event-body" x="561" y="883" text-anchor="end">social &amp;  community performance</text>

  <!-- 2022 -->
  <polyline class="connector s-2022" points="753,940 753,1110 1186,1110"/>
  <rect class="c-2022" x="718" y="913" width="90" height="27" rx="13.5"/>
  <circle class="node s-2022" cx="716" cy="926" r="4"/>
  <text class="year" x="763" y="934" text-anchor="middle">2022</text>
  <text class="event-title c-2022" x="816" y="929">Corvane Best of Business</text>
  <text class="event-body" x="816" y="949">Hollowmere wins the Corvane Best of Business Award (Vic) for building</text>
  <text class="event-body" x="816" y="965">communities</text>
  <text class="event-title c-2022" x="816" y="993">Move to Fernhurst</text>
  <text class="event-body" x="816" y="1012">Hollowmere moves to a larger premises in Fernhurst</text>
  <text class="event-title c-2022" x="816" y="1045">Partnerships</text>
  <text class="event-body" x="816" y="1063">Partnerships established with Tidewater School for Children with</text>
  <text class="event-body" x="816" y="1079">Disability &amp; Yarrow Circle (Eastbrook University)</text>

  <!-- 2023 -->
  <polyline class="connector s-2023" points="628,1040 628,1147 197,1147"/>
  <rect class="c-2023" x="580" y="1013" width="88" height="27" rx="13.5"/>
  <circle class="node s-2023" cx="670" cy="1026" r="4"/>
  <text class="year" x="624" y="1034" text-anchor="middle">2023</text>
  <text class="event-title c-2023" x="560" y="966" text-anchor="end">Reconciliation Action Plan (RAP)</text>
  <text class="event-body" x="559" y="983" text-anchor="end">Hollowmere’s Reflect RAP developed &amp; endorsed</text>
  <text class="event-title c-2023" x="560" y="1011" text-anchor="end">Client  Advisory Group</text>
  <text class="event-body" x="559" y="1028" text-anchor="end">Hollowmere’s Client Advisory Group commences</text>
  <text class="event-title c-2023" x="560" y="1057" text-anchor="end">E-Learning Platform</text>
  <text class="event-body" x="559" y="1074" text-anchor="end">Hollowmere e-learning launched</text>
  <text class="event-title c-2023" x="559" y="1104" text-anchor="end">Spectrum Mark</text>
  <text class="event-body" x="560" y="1120" text-anchor="end">Hollowmere achieves Spectrum Mark accreditation</text>
</svg>
</div>
</body>
</html>
```